Print materials for 3-star hotel

We are changing up our print materials (notepads, letterheads, key card jackets, small flyer for the room rates) We are a 3 star business hotel in the Philippines and have mainly used grey tones and clean, simple lines. See attached photos for logo and hotel interior photos.

Target Market(s)

Business

Contact Information for Business Card

Corvale Terrace Hotel
Lindwell Banca Avenue corner Tolenta St Cebu City 6000 Philippines
Tel: +63 32 481 7302
Mobile: +63 917 648 2095
www.corvaleterracehotel.example

Font styles to use
Serif
Sans Serif

Requirements
Must have
• Simple
• Readable font and font size
Nice to have
• Neutral colors, grey and taupes
Should not have
• No purples and bright blues

```html
<!DOCTYPE html>
<html lang="en">
<head>
<meta charset="utf-8">
<title>Corvale Terrace Hotel — Business Card</title>
<link rel="stylesheet" href="https://fonts.googleapis.com/css2?family=Cormorant+Garamond:wght@500;600&display=swap">
<style>
  :root {
    --backdrop: #e9eded;
    --card: #fbfbfa;
    --gold: #a8845c;
    --rule: #c9ab86;
    --shadow: rgba(60, 70, 70, 0.16);
  }
  * { margin: 0; padding: 0; box-sizing: border-box; }
  html, body {
    width: 1200px;
    height: 900px;
    overflow: hidden;
    background: var(--backdrop);
  }
  body {
    font-family: "Cormorant Garamond", "Times New Roman", serif;
    font-weight: 500;
    color: var(--gold);
    display: flex;
    align-items: center;
    justify-content: center;
    gap: 40px;
  }
  .card {
    position: relative;
    width: 540px;
    height: 308px;
    background: var(--card);
    box-shadow: 0 2px 3px var(--shadow), 0 18px 40px var(--shadow);
  }

  /* Front */
  .card-front {
    display: flex;
    align-items: center;
    justify-content: center;
  }
  .brand {
    display: flex;
    align-items: center;
    gap: 14px;
  }
  .brand-square {
    width: 14px;
    height: 14px;
    background: var(--gold);
  }
  .brand-name {
    font-size: 24px;
    letter-spacing: 0.26em;
    text-transform: uppercase;
    line-height: 1;
  }

  /* Back */
  .card-back .brand-small {
    position: absolute;
    top: 34px;
    right: 34px;
    font-size: 14px;
    letter-spacing: 0.26em;
    text-transform: uppercase;
  }
  .person {
    position: absolute;
    left: 34px;
    top: 100px;
  }
  .person-name {
    font-size: 26px;
    letter-spacing: 0.04em;
    text-transform: uppercase;
    line-height: 1;
  }
  .person-title {
    font-size: 14px;
    margin-top: 4px;
  }
  .rule {
    position: absolute;
    left: 34px;
    right: 34px;
    height: 1px;
    background: var(--rule);
  }
  .rule-top { top: 162px; }
  .rule-bottom { top: 258px; }
  .contact {
    position: absolute;
    left: 34px;
    right: 34px;
    top: 174px;
    font-size: 13px;
    font-weight: 600;
    line-height: 1.6;
    list-style: none;
    white-space: nowrap;
  }
  .contact-row {
    display: flex;
    gap: 16px;
  }
</style>
</head>
<body>
  <section class="card card-front" aria-label="Business card front">
    <div class="brand">
      <span class="brand-square"></span>
      <span class="brand-name">Corvale Terrace Hotel</span>
    </div>
  </section>

  <section class="card card-back" aria-label="Business card back">
    <div class="brand-small">Corvale Terrace</div>
    <div class="person">
      <p class="person-name">Elias Marbury</p>
      <p class="person-title">CEO/Founder</p>
    </div>
    <div class="rule rule-top"></div>
    <ul class="contact">
      <li>Lindwell Banca Avenue corner Tolenta St, Cebu City 6000 Philippines</li>
      <li class="contact-row"><span>Tel. +63 32 481 7302</span><span>Mobile. +63 917 648 2095</span><span>Email. info@corvale.example</span></li>
      <li>www.corvaleterracehotel.example</li>
    </ul>
    <div class="rule rule-bottom"></div>
  </section>
</body>
</html>
```